QVR business card

Need a business card for a company that provides instructional design and elearning development services. The website is here: http://quorvane.studio/

I'm attaching a current logo, as well as the old business card design. While I like to keep it clean, the old design is too simplistic for my liking. The only idea I want to reuse from the old design is placing industry jargon on the back of the card, just need a better way to present it. But if you have other ideas for the back--feel free to experiment.

Please use the colors complementary to the color we have on the website. Thank you!

```html
<!DOCTYPE html>
<html lang="en">
<head>
<meta charset="utf-8">
<title>QVR business card</title>
<link rel="stylesheet" href="https://fonts.googleapis.com/css2?family=Open+Sans:wght@400;600;700&family=PT+Sans+Narrow&display=swap">
<style>
  :root {
    --backdrop: #2e2825;
    --card-black: #111112;
    --teal: #1fb8b3;
    --teal-light: #3cc9c3;
    --gold: #c9b57a;
    --white: #ffffff;
    --rule: #5a5a5c;
  }
  * { margin: 0; padding: 0; box-sizing: border-box; }
  html, body { width: 1200px; height: 814px; overflow: hidden; }
  body {
    background: var(--backdrop);
    font-family: "Open Sans", Arial, sans-serif;
    position: relative;
  }
  .card {
    position: absolute;
    top: 252px;
    width: 540px;
    height: 309px;
    border-radius: 3px;
    overflow: hidden;
    box-shadow: 0 10px 30px rgba(0,0,0,.45);
  }
  /* Front */
  .card-front { left: 45px; background: var(--card-black); }
  .brand {
    position: absolute;
    left: 62px;
    top: 166px;
    display: flex;
    align-items: center;
    gap: 12px;
  }
  .brand-square { width: 22px; height: 22px; background: var(--teal); }
  .brand-name {
    color: var(--gold);
    font-weight: 600;
    font-size: 40px;
    letter-spacing: 2px;
    line-height: 1;
  }
  .divider-front {
    position: absolute;
    left: 262px; top: 70px;
    width: 1px; height: 170px;
    background: linear-gradient(var(--card-black), var(--rule) 25%, var(--rule) 75%, var(--card-black));
  }
  .contact { position: absolute; left: 282px; top: 86px; }
  .person-name { color: var(--teal); font-weight: 600; font-size: 19px; line-height: 1.2; }
  .person-role { color: var(--gold); font-size: 13px; margin-top: 2px; }
  .contact-list { list-style: none; margin-top: 22px; }
  .contact-list li {
    display: flex; align-items: center; gap: 8px;
    color: var(--white); font-size: 12.5px; line-height: 20px;
  }
  .contact-list svg { width: 12px; height: 12px; flex: none; }

  /* Back */
  .card-back { left: 615px; background: var(--teal); }
  .headline {
    position: absolute; left: 26px; top: 26px;
    color: var(--white); font-weight: 600; line-height: 1;
  }
  .headline span { display: block; }
  .hl-how { font-size: 50px; letter-spacing: 8px; }
  .hl-can { font-size: 56px; letter-spacing: 4px; margin-top: 6px; }
  .hl-we { font-size: 82px; letter-spacing: 2px; margin-top: 2px; }
  .hl-help { font-size: 48px; letter-spacing: 2px; margin-top: 2px; }
  .divider-back {
    position: absolute; left: 212px; top: 28px;
    width: 2px; height: 252px; background: rgba(255,255,255,.75);
  }
  .jargon {
    position: absolute; left: 226px; top: 26px;
    list-style: none;
    font-family: "PT Sans Narrow", "Arial Narrow", sans-serif;
    color: var(--white); font-size: 27px; line-height: 43px;
    text-transform: uppercase; white-space: nowrap;
  }
</style>
</head>
<body>
  <section class="card card-front">
    <div class="brand">
      <span class="brand-square"></span>
      <span class="brand-name">QVR</span>
    </div>
    <div class="divider-front"></div>
    <div class="contact">
      <p class="person-name">Marek Vantrell</p>
      <p class="person-role">CEO/Founder</p>
      <ul class="contact-list">
        <li>
          <svg viewBox="0 0 12 12" aria-hidden="true"><path fill="#fff" d="M2.4 1 4.3 2.9 3.4 4.3c.8 1.7 2.2 3.1 4 4l1.3-1L10.9 9.4 9.6 11C5 10.6 1.4 7 1 2.4Z"/></svg>
          555-014-2287
        </li>
        <li>
          <svg viewBox="0 0 12 12" aria-hidden="true"><rect x="1" y="2.5" width="10" height="7" fill="#fff"/><path d="M1 2.5 6 6.5 11 2.5" fill="none" stroke="#111" stroke-width="1"/></svg>
          mvantrell@quorvane.studio
        </li>
        <li>
          <svg viewBox="0 0 12 12" aria-hidden="true"><circle cx="6" cy="6" r="5" fill="#fff"/><path d="M1 6h10M6 1c-2 2.8-2 7.2 0 10M6 1c2 2.8 2 7.2 0 10" fill="none" stroke="#111" stroke-width=".8"/></svg>
          www.quorvane.studio
        </li>
      </ul>
    </div>
  </section>

  <section class="card card-back">
    <h2 class="headline">
      <span class="hl-how">HOW</span>
      <span class="hl-can">CAN</span>
      <span class="hl-we">WE</span>
      <span class="hl-help">HELP?</span>
    </h2>
    <div class="divider-back"></div>
    <ul class="jargon">
      <li>Mobile Learning SCORM</li>
      <li>Instructional Design LMS</li>
      <li>MOOCs eLearning HTML5</li>
      <li>Adult Learning Theory</li>
      <li>Gamification Classroom</li>
      <li>xAPI Blended Learning</li>
    </ul>
  </section>
</body>
</html>
```